Black Matte card with samurai logo which I would like it to be textured and company name on one side and on the other side I would like the company information with the reno (Face logo) Sushi logo. Double Sided card.

majority customers are University students, University sororities and fraternities.

It Company

Reno Sushi
317 W. Harlow Ave
Tucson, AZ 85042
Phone (520)413-6271
Fax (520)357-1846
E-mail: Renosushidesert@mailbox-example.com
FB: Renosushidesert
Twitter: Renosushidesert

• Present Normal

```html
<!DOCTYPE html>
<html lang="en">
<head>
<meta charset="utf-8">
<title>Reno Sushi – Business Card</title>
<link rel="stylesheet" href="https://fonts.googleapis.com/css2?family=PT+Sans:wght@400&display=swap">
<style>
  :root {
    --stage: #ebe7e1;
    --card-black: #1e1c1c;
    --card-black-deep: #121111;
    --card-white: #ffffff;
    --band-red: #b3261e;
    --brand-red: #a5271f;
    --ink-white: #ffffff;
    --art-dark: #2a2626;
    --art-red: #9e2a22;
  }
  * { box-sizing: border-box; margin: 0; padding: 0; }
  html, body {
    width: 1200px;
    height: 1041px;
    overflow: hidden;
    background: var(--stage);
    font-family: "PT Sans", sans-serif;
  }
  .card {
    position: absolute;
    width: 787px;
    height: 450px;
    border-radius: 32px;
    overflow: hidden;
  }
  /* Back side: textured black */
  .card--back {
    left: 44px;
    top: 56px;
    background:
      radial-gradient(circle at 30% 20%, rgba(255,255,255,0.05), transparent 60%),
      repeating-linear-gradient(45deg, rgba(255,255,255,0.025) 0 2px, transparent 2px 5px),
      repeating-linear-gradient(-45deg, rgba(0,0,0,0.2) 0 2px, transparent 2px 6px),
      linear-gradient(160deg, var(--card-black), var(--card-black-deep));
  }
  .card--back .mascot-art {
    position: absolute;
    left: 222px;
    top: 35px;
    width: 345px;
    height: 315px;
    background: radial-gradient(circle at 50% 45%, #f2f2f2 0%, #d9d9d9 45%, rgba(200,60,50,0.55) 80%, transparent 100%);
    border-radius: 12px;
  }
  .card--back .website {
    position: absolute;
    left: 0;
    right: 0;
    top: 380px;
    text-align: center;
    color: var(--ink-white);
    font-size: 21px;
    letter-spacing: 1.2px;
  }
  /* Front side: white with black curved footer */
  .card--front {
    left: 362px;
    top: 538px;
    background: var(--card-white);
  }
  .card--front .footer-shape {
    position: absolute;
    inset: 0;
  }
  .card--front .mascot-art {
    position: absolute;
    left: 320px;
    top: 29px;
    width: 166px;
    height: 148px;
    background: radial-gradient(circle at 50% 50%, var(--art-dark) 0%, #4a3a38 55%, rgba(158,42,34,0.6) 85%, transparent 100%);
    border-radius: 8px;
  }
  .brand-name {
    position: absolute;
    left: 0;
    right: 0;
    top: 176px;
    text-align: center;
    color: var(--brand-red);
    font-weight: 400;
    line-height: 1;
  }
  .brand-name .brand-main { display: block; font-size: 54px; }
  .brand-name .brand-sub { display: block; font-size: 24px; margin-top: 2px; }
  .contact {
    position: absolute;
    left: 0;
    right: 0;
    top: 322px;
    color: var(--ink-white);
    font-size: 20px;
    text-align: center;
  }
  .contact__line {
    display: flex;
    justify-content: center;
    align-items: center;
    gap: 8px;
    height: 31px;
  }
  .contact__item { display: inline-flex; align-items: center; gap: 8px; }
  .contact__item + .contact__item { margin-left: 10px; }
  .icon { width: 17px; height: 17px; flex: none; }
  .social-square {
    width: 17px;
    height: 17px;
    border-radius: 3px;
    flex: none;
  }
  .social-square--fb { background: #3b5a9a; }
  .social-square--tw { background: #4fa8d8; }
</style>
</head>
<body>

<section class="card card--back">
  <div class="mascot-art" role="img" aria-label="Samurai mascot illustration holding a sword and a fish"></div>
  <p class="website">www.renosushidesert.com</p>
</section>

<section class="card card--front">
  <svg class="footer-shape" viewBox="0 0 787 450" width="787" height="450" aria-hidden="true">
    <path d="M0 226 Q393 336 787 226 L787 246 Q393 354 0 246 Z" fill="var(--band-red)"/>
    <path d="M0 244 Q393 352 787 244 L787 450 L0 450 Z" fill="var(--card-black)"/>
  </svg>

  <div class="mascot-art" role="img" aria-label="Small samurai mascot illustration"></div>

  <h1 class="brand-name">
    <span class="brand-main">reno</span>
    <span class="brand-sub">sushi</span>
  </h1>

  <address class="contact">
    <div class="contact__line">
      <span class="contact__item">
        <svg class="icon" viewBox="0 0 24 24" aria-hidden="true"><path fill="#fff" d="M6.6 10.8a15.1 15.1 0 0 0 6.6 6.6l2.2-2.2a1 1 0 0 1 1-.25 11.4 11.4 0 0 0 3.6.57 1 1 0 0 1 1 1V20a1 1 0 0 1-1 1A17 17 0 0 1 3 4a1 1 0 0 1 1-1h3.5a1 1 0 0 1 1 1c0 1.25.2 2.45.57 3.57a1 1 0 0 1-.25 1z"/></svg>
        (520)413-6271
      </span>
      <span class="contact__item">
        <svg class="icon" viewBox="0 0 24 24" aria-hidden="true"><rect x="6" y="1" width="12" height="22" rx="2" fill="#fff"/><rect x="8" y="4" width="8" height="10" fill="#1e1c1c"/><rect x="8" y="16" width="8" height="5" fill="#888"/></svg>
        (520)357-1846
      </span>
    </div>
    <div class="contact__line">
      <span class="contact__item">
        <svg class="icon" viewBox="0 0 24 24" aria-hidden="true"><rect x="2" y="6" width="20" height="13" rx="2" fill="#fff"/><path d="M2 7l10 7 10-7" fill="none" stroke="#1e1c1c" stroke-width="1.8"/></svg>
        Renosushidesert@mailbox-example.com
      </span>
    </div>
    <div class="contact__line">
      <span class="contact__item"><span class="social-square social-square--fb"></span>Renosushidesert</span>
      <span class="contact__item"><span class="social-square social-square--tw"></span>Renosushidesert</span>
    </div>
    <div class="contact__line">
      <span class="contact__item">Reno Sushi 317 W. Harlow Ave Tucson, AZ 85042</span>
    </div>
  </address>
</section>

</body>
</html>
```